tinyTally Resource Book - 10 maths tasks to do outside

I need a 22 (11 pages back to back) page A6 sized book produced to standard for submission to professional printer. Needs to be as .pdf file showing guide lines and allowances for colour bleed. I have text already written and submitted as attachment in a Word file with margins set to A6 size. The theme of the materials is "Nature Play" so using lots of pictures from nature (Australia preferably) and showing lots of patterns in nature (rocks, leaves, flower petals etc). Some of the tasks refer to specific activities, such as "shadows" and "floating" so would be great to illustrate appropriately. The big emphasis is on learning outside the classroom, getting kids to engage actively with nature. I would like to see the pages as full colour - so not white background. The book itself will be spiral bound along the top edge so a margin of at least 1cm will be required at the top of each page (or the bottom of even numbered pages). Book will be printed on plastic laminated matte paper for outdoor use. Font size needs to be big enough to read. Fonts sizes, alignments and page numbers are all different at the moment and need to be standardised. One photo is included in a page as a sample if you can use it, otherwise disregard. Logo for Wattlebrook Numeracy Guild is also included to have as part of the acknowledgements at the back of the book.

Target Market(s)

Book is for early childhood and preschool teachers.

Industry/Entity Type

Education

Font styles to use
Sans Serif

Requirements
Must have
• Colour and appeal.
Nice to have
• Use of natural colours instead of bright catchy colours but that is your call.
Should not have
• American spelling

```html
<!DOCTYPE html>
<html lang="en-GB">
<head>
<meta charset="utf-8">
<title>5. Shadows</title>
<link rel="stylesheet" href="https://fonts.googleapis.com/css2?family=Didact+Gothic&family=Nunito:wght@900&display=swap">
<style>
  :root {
    --paper: #ffffff;
    --wood-light: #f1c88f;
    --wood-mid: #e9b878;
    --wood-dark: #dca766;
    --heading: #2c3889;
    --heading-edge: #ffffff;
    --bullet: #d7262c;
    --body: #3a3430;
    --trim: #8a8a8a;
  }
  * { box-sizing: border-box; margin: 0; padding: 0; }
  html, body { width: 892px; height: 1200px; overflow: hidden; background: var(--paper); }
  .sheet { position: relative; width: 892px; height: 1200px; }
  .crop-marks { position: absolute; inset: 0; }
  .page {
    position: absolute; left: 54px; top: 56px; width: 786px; height: 1092px;
    background:
      repeating-linear-gradient(90deg, rgba(255,255,255,0.08) 0 6px, rgba(160,100,40,0.05) 6px 11px, rgba(255,255,255,0) 11px 23px),
      linear-gradient(90deg, var(--wood-mid), var(--wood-light) 30%, var(--wood-dark) 55%, var(--wood-light) 80%, var(--wood-mid));
  }
  .heading {
    position: absolute; left: 72px;
    font-family: "Nunito", sans-serif; font-weight: 900; color: var(--heading);
    -webkit-text-stroke: 5px var(--heading-edge); paint-order: stroke fill;
    line-height: 1; white-space: nowrap;
  }
  .heading--title { font-size: 53px; top: 86px; }
  .heading--section { font-size: 44px; }
  .list {
    position: absolute; left: 164px; list-style: none; white-space: nowrap;
    font-family: "Didact Gothic", sans-serif; font-size: 32.5px; line-height: 39px; color: var(--body);
  }
  .list li { position: relative; }
  .list li::before {
    content: ""; position: absolute; left: -34px; top: 11px;
    width: 17px; height: 17px; background: var(--bullet); transform: rotate(45deg);
  }
  .still-life {
    position: absolute; left: 394px; top: 768px; width: 290px; height: 244px;
    border-radius: 40px;
    background: radial-gradient(ellipse at 45% 55%, rgba(150,120,95,0.45), rgba(200,150,100,0.15) 70%, rgba(0,0,0,0) 100%);
  }
</style>
</head>
<body>
<div class="sheet">
  <section class="page">
    <h1 class="heading heading--title">5. Shadows</h1>
    <ul class="list" style="top:145px">
      <li>Draw the outline of the shadow of a<br>tree, plant, person, toy, building etc<br>using coloured chalk, a stick in sand etc</li>
      <li>Revisit at different times of day and<br>redraw using different coloured chalk etc<br>to show change</li>
    </ul>

    <h2 class="heading heading--section" style="top:400px">Prompting questions</h2>
    <ul class="list" style="top:453px">
      <li>How does the shadow change?</li>
      <li>How do you make a shadow?</li>
    </ul>

    <h2 class="heading heading--section" style="top:551px">Variations</h2>
    <ul class="list" style="top:604px">
      <li>Make a “shadow gallery” in sandpit or<br>garden</li>
      <li>Take photos of shadows</li>
      <li>Trace shadows onto large sheets<br>of paper</li>
      <li>Play shadow tag</li>
    </ul>

    <h2 class="heading heading--section" style="top:860px">Big Ideas</h2>
    <ul class="list" style="top:912px">
      <li>Shape</li>
      <li>Change</li>
      <li>Time</li>
    </ul>

    <div class="still-life" role="img" aria-label="Photo of an apple, a drink bottle and two rocks casting shadows"></div>
  </section>

  <svg class="crop-marks" width="892" height="1200" viewBox="0 0 892 1200" stroke="var(--trim)" stroke-width="1" fill="none">
    <path d="M54 0V36M0 54H36M74 36V74M36 74H74"/>
    <path d="M840 0V36M892 54H856M818 36V74M856 74H818"/>
    <path d="M54 1200V1164M0 1148H36M74 1164V1126M36 1126H74"/>
    <path d="M840 1200V1164M892 1148H856M818 1164V1126M856 1126H818"/>
  </svg>
</div>
</body>
</html>
```